Kestrel Facilities Business Card Design

We would now like to design business cards with the new Kestrel Facilities logo

Target Market(s)

Professional

Industry/Entity Type

Professional services

Contact Information for Business Card

Employee name, title, phone number, email address, corporate office address and logo.

Font styles to use
Sans Serif

Colors
0054AA
0677BA
7BADD7
CADEEF
E8F1F8

Requirements
Must have
• My logo
Should not have
• any other pictures or images besides my logo

```html
<!DOCTYPE html>
<html lang="en">
<head>
<meta charset="utf-8">
<title>Kestrel Facilities Business Card</title>
<link href="https://fonts.googleapis.com/css2?family=Montserrat:wght@400;500;700&display=swap" rel="stylesheet">
<style>
  :root {
    --brand-blue: #3677be;
    --line-blue: #2f6fb8;
    --stripe-grey: #a9a9ab;
    --card-white: #ffffff;
    --ink: #1c1c1c;
    --mark-silver: #d2d6dc;
    --backdrop: #e6e7e9;
  }
  * { margin: 0; padding: 0; box-sizing: border-box; }
  html, body { width: 1200px; height: 813px; overflow: hidden; }
  body {
    background: var(--backdrop);
    font-family: "Montserrat", sans-serif;
    display: flex;
    align-items: center;
    justify-content: center;
    gap: 40px;
  }
  .card {
    position: relative;
    width: 540px;
    height: 310px;
    border-radius: 22px;
    overflow: hidden;
  }
  .card-front { background: var(--card-white); }
  .card-back {
    background: var(--brand-blue);
    display: flex;
    align-items: center;
    justify-content: center;
  }
  .wave { position: absolute; inset: 0; width: 100%; height: 100%; }
  .brand {
    position: absolute;
    left: 28px;
    top: 112px;
    width: 200px;
    display: flex;
    align-items: center;
    gap: 10px;
    color: var(--brand-blue);
    font-weight: 700;
    font-size: 21px;
    line-height: 1.1;
  }
  .brand-square {
    flex: none;
    width: 26px;
    height: 26px;
    background: var(--brand-blue);
  }
  .divider {
    position: absolute;
    left: 238px;
    top: 40px;
    width: 1.5px;
    height: 170px;
    background: var(--line-blue);
  }
  .details {
    position: absolute;
    left: 256px;
    top: 34px;
    color: var(--ink);
    font-size: 12.5px;
    line-height: 1.35;
  }
  .person-name {
    color: var(--brand-blue);
    font-weight: 700;
    font-size: 19px;
    letter-spacing: 0.3px;
    line-height: 1.1;
  }
  .person-title { font-size: 13px; margin-bottom: 12px; }
  .address { margin-bottom: 12px; }
  .contact { list-style: none; }
  .contact li { display: flex; align-items: center; gap: 7px; }
  .contact svg { width: 12px; height: 12px; fill: var(--brand-blue); flex: none; }
  .back-brand {
    display: flex;
    align-items: center;
    gap: 14px;
    color: var(--mark-silver);
    font-weight: 700;
    font-size: 34px;
  }
  .back-brand .brand-square { width: 38px; height: 38px; background: var(--mark-silver); }
</style>
</head>
<body>
  <section class="card card-front">
    <svg class="wave" viewBox="0 0 540 310" preserveAspectRatio="none" aria-hidden="true">
      <path d="M150 310 C190 240 300 225 420 190 C500 165 525 110 540 60 L540 310 Z" fill="var(--stripe-grey)"/>
      <path d="M162 310 C200 250 305 236 425 200 C505 175 532 122 540 84 L540 310 Z" fill="var(--card-white)"/>
      <path d="M170 310 C208 256 310 242 428 207 C508 182 535 130 540 98 L540 310 Z" fill="var(--brand-blue)"/>
    </svg>
    <div class="brand"><span class="brand-square"></span><span>Kestrel Facilities</span></div>
    <div class="divider"></div>
    <div class="details">
      <p class="person-name">DANA WHITFIELD</p>
      <p class="person-title">Co-Founder</p>
      <p class="address">1840 N. Harbor Lane<br>Suite 410 Brookfield 32</p>
      <ul class="contact">
        <li><svg viewBox="0 0 24 24"><path d="M6.6 10.8a15 15 0 0 0 6.6 6.6l2.2-2.2a1 1 0 0 1 1-.25 11.4 11.4 0 0 0 3.6.57 1 1 0 0 1 1 1V20a1 1 0 0 1-1 1A17 17 0 0 1 3 4a1 1 0 0 1 1-1h3.5a1 1 0 0 1 1 1c0 1.25.2 2.45.57 3.57a1 1 0 0 1-.25 1z"/></svg>+254-300-41725</li>
        <li><svg viewBox="0 0 24 24"><path d="M2 5h20v14H2z M2 5l10 8 10-8" stroke="#fff" stroke-width="1.5"/></svg>info@kestrelfac.com</li>
        <li><svg viewBox="0 0 24 24"><circle cx="12" cy="12" r="10"/></svg>www.kestrelfac.com</li>
      </ul>
    </div>
  </section>
  <section class="card card-back">
    <div class="back-brand"><span class="brand-square"></span><span>Kestrel Facilities</span></div>
  </section>
</body>
</html>
```